Website Design for a holiday home letting busines

We require a redesign of our present website www.pinebrookstays.com. We want the website to stand out and look professional and clean to make holiday hunters want to book a caravan or lodge holiday with us. Our logo is red however we DO NOT want the website to be red. We want a natural colour scheme.

The final design should communicate that we are a professional company to book with.

On the home page we require;
Overview of company
Photo
Search box for holiday (check in)
Late Deals
Reviews
News

We would like the following pages designed; home page, available dates page, caravans page, content page.

The website should be responsive for smart phones. One website I do like is http://www.verdoliso.be/nl/

Target Market(s)

Families

Industry/Entity Type

Travel

Number of Pages Required

5+ page

Font styles to use
Serif

Requirements
Must have
• The project must be responsive for mobile phones and tablets.
• Ability to search for holiday home holidays
• We want a natural colour scheme.
Nice to have
• A style we like is http://www.verdoliso.be/nl/
Should not have
• Do not use red as a colour for the website. Our logo is red so this is the only time we want this used.

```html
<!DOCTYPE html>
<html lang="en">
<head>
<meta charset="utf-8">
<title>Pinebrook Stays – Private Holiday Rentals</title>
<link href="https://fonts.googleapis.com/css2?family=Open+Sans:wght@400;600;700;800&display=swap" rel="stylesheet">
<style>
:root{
  --teal:#1fb8bd;
  --teal-dark:#17979b;
  --ink:#2a2a2a;
  --text:#555;
  --muted:#8a8a8a;
  --line:#e3e3e3;
  --bg:#ffffff;
  --nav:#262626;
  --nav-bar:#3a3a3a;
  --footer:#2b2b2b;
  --footer-deep:#1e1e1e;
  --brand:#d3262b;
}
*{box-sizing:border-box;margin:0;padding:0}
html,body{width:703px;height:1200px;overflow:hidden;background:var(--bg)}
body{font-family:"Open Sans",Arial,sans-serif;color:var(--text);font-size:8px;position:relative}
.site{position:relative;width:703px;height:1200px;overflow:hidden}
/* header */
.header{position:absolute;top:0;left:0;right:0;height:61px;display:flex;align-items:center;padding:0 42px 0 28px}
.brand{display:flex;align-items:center;gap:7px;width:240px}
.brand-mark{width:22px;height:22px;background:var(--brand)}
.brand-name{font-size:15px;font-weight:700;color:var(--brand);line-height:1}
.brand-sub{font-size:7px;color:var(--muted);margin-top:3px}
.contact-strip{display:flex;gap:26px;margin-left:auto}
.contact-item{display:flex;gap:6px;align-items:flex-start}
.contact-item svg{flex:none}
.contact-item p{font-size:7px;line-height:1.45;color:var(--muted)}
.contact-item strong{color:var(--ink);font-weight:600}
/* nav */
.nav{position:absolute;top:61px;left:0;right:0;height:23px;background:var(--nav-bar);display:flex;padding-left:62px}
.nav a{color:#e6e6e6;text-decoration:none;font-size:7.5px;font-weight:600;padding:0 14px;display:flex;align-items:center}
.nav a.active{background:var(--nav);color:#fff}
/* hero */
.hero{position:absolute;top:84px;left:0;right:0;height:290px;background:linear-gradient(180deg,#7fb9d6 0%,#a9d3e4 32%,#4fb4c2 52%,#d9cdb5 78%,#c7b59a 100%)}
.hero-copy{position:absolute;left:58px;top:70px;color:#fff}
.hero-copy h1{font-size:21px;font-weight:800;letter-spacing:.3px}
.hero-copy p{font-size:9px;line-height:1.55;margin-top:8px;width:190px}
/* search */
.search{position:absolute;top:366px;left:76px;width:540px;height:70px;background:#2f2f2f;box-shadow:0 2px 6px rgba(0,0,0,.25)}
.search-tabs{display:flex;height:22px}
.search-tabs span{flex:1;background:var(--teal);color:#fff;font-size:7px;display:flex;align-items:center;justify-content:center;border-left:1px solid var(--teal-dark)}
.search-tabs span.title{background:#222;flex:.85;border:0}
.search-row{display:flex;gap:10px;padding:12px 14px;align-items:center}
.select{flex:1;height:15px;background:#fff;border-radius:2px;font-size:6px;color:var(--muted);display:flex;align-items:center;justify-content:space-between;padding:0 5px}
.search-btn{width:50px;height:17px;background:var(--teal);color:#fff;font-size:7px;border-radius:2px;display:flex;align-items:center;justify-content:center}
/* main */
.section-title{position:absolute;left:56px;font-size:13px;color:var(--ink);font-weight:600}
.cards{position:absolute;left:56px;display:flex;gap:14px}
.card{width:134px}
.card-photo{height:60px}
.card-title{font-size:7px;font-weight:600;color:var(--ink);margin:6px 0 4px}
.card-row{display:flex;justify-content:space-between;font-size:6px;color:var(--muted);line-height:1.9;border-top:1px solid var(--line)}
.card-row b{color:var(--ink);font-weight:600}
.card-row .ic{color:var(--teal);margin-right:3px}
.ph-a{background:linear-gradient(135deg,#cbb79a,#8b6f52)}
.ph-b{background:linear-gradient(135deg,#e8e2d8,#9aa6b8)}
.ph-c{background:linear-gradient(135deg,#6b5140,#c9b8a2)}
.ph-d{background:linear-gradient(135deg,#b98a5a,#f0d9b6)}
.ph-e{background:linear-gradient(135deg,#8a5c3b,#d8b48c)}
.ph-f{background:linear-gradient(135deg,#d9d0c2,#7f8e74)}
.reviews{position:absolute;left:56px;top:882px;display:flex;gap:12px}
.review{width:210px;height:52px;border:1px solid var(--line);padding:7px 10px;background:#fafafa}
.review h4{font-size:7px;color:var(--teal);font-weight:600}
.review .stay{font-size:6px;color:var(--ink);margin:2px 0 3px}
.review p{font-size:6px;line-height:1.5;color:var(--muted)}
/* sidebar */
.sidebar{position:absolute;left:496px;width:150px}
.side-box{border:1px solid var(--line);padding:8px;background:#fff;box-shadow:0 1px 3px rgba(0,0,0,.06)}
.side-box h3{font-size:10px;color:var(--ink);font-weight:600;margin-bottom:8px}
.blog-item{display:flex;gap:6px;margin-bottom:9px}
.blog-thumb{width:22px;height:22px;flex:none}
.blog-item h5{font-size:5.5px;color:var(--ink);font-weight:700}
.blog-item p{font-size:5px;color:var(--muted);line-height:1.4}
.blog-item .meta{color:var(--teal)}
.news-item{display:flex;gap:7px;margin-bottom:9px}
.date{width:26px;height:30px;background:var(--teal);color:#fff;text-align:center;flex:none;padding-top:3px}
.date b{display:block;font-size:11px;line-height:1.1}
.date span{font-size:5px}
.news-item h5{font-size:5.5px;font-weight:700;color:var(--ink)}
.news-item p{font-size:5px;color:var(--muted);line-height:1.4}
.news-item .meta{color:var(--teal)}
/* footer */
.footer{position:absolute;top:940px;left:0;right:0;height:220px;background:var(--footer);display:flex;padding:18px 56px 0;gap:28px;color:#bdbdbd}
.footer h4{font-size:9px;color:#fff;font-weight:700;margin-bottom:10px;letter-spacing:.2px}
.footer p{font-size:6.5px;line-height:2.1}
.f-col{width:120px}
.map{width:118px;height:72px;background:linear-gradient(135deg,#e7e3d6,#c9d8c0)}
.news-input{width:126px;height:15px;background:#fff;border-radius:2px;margin-top:8px;font-size:6px;color:var(--muted);padding:4px}
.news-btn{width:46px;height:14px;background:var(--teal);color:#fff;font-size:6px;display:flex;align-items:center;justify-content:center;margin-top:6px;border-radius:2px}
.feed-item{display:flex;gap:6px;margin-bottom:8px}
.feed-avatar{width:20px;height:20px;background:#555;flex:none}
.feed-item p{line-height:1.5;font-size:5.5px}
.bottom-bar{position:absolute;top:1160px;left:0;right:0;height:40px;background:var(--footer-deep);color:#8a8a8a;font-size:6px;display:flex;align-items:center;justify-content:center}
.side-tab{position:absolute;right:0;top:1066px;width:13px;height:48px;background:var(--teal);color:#fff;font-size:6px;writing-mode:vertical-rl;display:flex;align-items:center;justify-content:center}
</style>
</head>
<body>
<div class="site">
  <header class="header">
    <div class="brand">
      <div class="brand-mark"></div>
      <div>
        <div class="brand-name">Pinebrook Stays</div>
        <div class="brand-sub">at Pinebrook Holiday Park</div>
      </div>
    </div>
    <div class="contact-strip">
      <div class="contact-item">
        <svg width="9" height="11" viewBox="0 0 10 12"><path d="M5 0a4 4 0 0 0-4 4c0 3 4 8 4 8s4-5 4-8a4 4 0 0 0-4-4zm0 5.5A1.5 1.5 0 1 1 5 2.5a1.5 1.5 0 0 1 0 3z" fill="#1fb8bd"/></svg>
        <p><strong>Pinebrook Stays Ltd</strong><br>12 Fernhill Lane, P1</p>
      </div>
      <div class="contact-item">
        <svg width="10" height="10" viewBox="0 0 10 10"><path d="M2 0l2 2.5-1 1.3a6 6 0 0 0 3.2 3.2L7.5 6 10 8 8.6 9.6C4.5 9.8.2 5.5.4 1.4z" fill="#1fb8bd"/></svg>
        <p><strong>01632 960 418</strong><br>hello@pinebrookstays.com</p>
      </div>
      <div class="contact-item">
        <svg width="10" height="10" viewBox="0 0 10 10"><circle cx="5" cy="5" r="4.3" fill="none" stroke="#1fb8bd" stroke-width="1.2"/><path d="M5 2.5V5l1.8 1.2" stroke="#1fb8bd" stroke-width="1" fill="none"/></svg>
        <p><strong>Monday-Friday</strong><br>9:00 am - 5:00 pm</p>
      </div>
    </div>
  </header>

  <nav class="nav">
    <a class="active">Home</a><a>Reviews</a><a>Locations</a><a>2015 Holidays</a><a>2016 Holidays</a><a>Payment Plans</a><a>Contact Us</a>
  </nav>

  <section class="hero" role="img" aria-label="Two wooden deck chairs with holiday hats on a tropical beach by turquoise sea">
    <div class="hero-copy">
      <h1>PRIVATE HOLIDAY RENTALS</h1>
      <p>Quality Lodge &amp; Caravan hire at Pinebrook Holiday Park. Book online today!<br>More details</p>
    </div>
  </section>

  <form class="search">
    <div class="search-tabs">
      <span class="title">Search function</span><span>Locations</span><span>Locations</span><span>Locations</span>
    </div>
    <div class="search-row">
      <div class="select">Arrival <span>▾</span></div>
      <div class="select">Nights <span>▾</span></div>
      <div class="select">Adults <span>▾</span></div>
      <div class="select">Any Lodge <span>▾</span></div>
      <div class="search-btn">Search</div>
    </div>
  </form>

  <h2 class="section-title" style="top:456px">Our caravans and lodges</h2>
  <div class="cards" style="top:485px">
    <article class="card"><div class="card-photo ph-a" role="img" aria-label="Lodge bedroom interior"></div><div class="card-title">New Hampshire</div>
      <div class="card-row"><span><span class="ic">■</span>Beds</span><b>3</b></div><div class="card-row"><span><span class="ic">■</span>Baths</span><b>2</b></div><div class="card-row"><span><span class="ic">■</span>Area</span><b>100 sqft</b></div></article>
    <article class="card"><div class="card-photo ph-b" role="img" aria-label="Bright caravan bedroom"></div><div class="card-title">New Hampshire</div>
      <div class="card-row"><span><span class="ic">■</span>Beds</span><b>2</b></div><div class="card-row"><span><span class="ic">■</span>Baths</span><b>1</b></div><div class="card-row"><span><span class="ic">■</span>Area</span><b>100 sqft</b></div></article>
    <article class="card"><div class="card-photo ph-c" role="img" aria-label="Lodge living room interior"></div><div class="card-title">New Hampshire</div>
      <div class="card-row"><span><span class="ic">■</span>Beds</span><b>3</b></div><div class="card-row"><span><span class="ic">■</span>Baths</span><b>2</b></div><div class="card-row"><span><span class="ic">■</span>Area</span><b>100 sqft</b></div></article>
  </div>

  <h2 class="section-title" style="top:660px">Late Deals</h2>
  <div class="cards" style="top:688px">
    <article class="card"><div class="card-photo ph-d" role="img" aria-label="Cosy lounge with fireplace"></div><div class="card-title">New Hampshire</div>
      <div class="card-row"><span><span class="ic">■</span>Beds</span><b>3</b></div><div class="card-row"><span><span class="ic">■</span>Baths</span><b>2</b></div><div class="card-row"><span><span class="ic">■</span>Area</span><b>100 sqft</b></div></article>
    <article class="card"><div class="card-photo ph-e" role="img" aria-label="Warm lodge bedroom"></div><div class="card-title">New Hampshire</div>
      <div class="card-row"><span><span class="ic">■</span>Beds</span><b>2</b></div><div class="card-row"><span><span class="ic">■</span>Baths</span><b>1</b></div><div class="card-row"><span><span class="ic">■</span>Area</span><b>100 sqft</b></div></article>
    <article class="card"><div class="card-photo ph-f" role="img" aria-label="Caravan dining area"></div><div class="card-title">New Hampshire</div>
      <div class="card-row"><span><span class="ic">■</span>Beds</span><b>3</b></div><div class="card-row"><span><span class="ic">■</span>Baths</span><b>2</b></div><div class="card-row"><span><span class="ic">■</span>Area</span><b>100 sqft</b></div></article>
  </div>

  <h2 class="section-title" style="top:856px">Latest reviews</h2>
  <div class="reviews">
    <div class="review"><h4>Clara Hensley</h4><div class="stay">Stayed in Pine Lodge, August</div><p>A lovely clean lodge with everything we needed. The children loved the park and we will book again next year.</p></div>
    <div class="review"><h4>Clara Hensley</h4><div class="stay">Stayed in Birch Caravan, July</div><p>Friendly service, easy booking and a spotless caravan close to the beach. A perfect family week away.</p></div>
  </div>

  <aside class="sidebar" style="top:492px">
    <div class="side-box">
      <h3>Latest Blog</h3>
      <div class="blog-item"><div class="blog-thumb ph-a" role="img" aria-label="Lodge thumbnail"></div><div><h5>THE PARK RETREAT</h5><p>Short note on our latest lodge upgrades</p><p class="meta">12 Dec · Comments</p></div></div>
      <div class="blog-item"><div class="blog-thumb ph-b" role="img" aria-label="Caravan thumbnail"></div><div><h5>THE PARK RETREAT</h5><p>Short note on our latest lodge upgrades</p><p class="meta">12 Dec · Comments</p></div></div>
      <div class="blog-item"><div class="blog-thumb ph-c" role="img" aria-label="Interior thumbnail"></div><div><h5>THE PARK RETREAT</h5><p>Short note on our latest lodge upgrades</p><p class="meta">12 Dec · Comments</p></div></div>
    </div>
  </aside>

  <aside class="sidebar" style="top:752px">
    <div class="side-box">
      <h3>Latest News</h3>
      <div class="news-item"><div class="date"><b>08</b><span>December</span></div><div><h5>TRENDING NEWS</h5><p>New lodges open for the spring season</p><p class="meta">Comments</p></div></div>
      <div class="news-item"><div class="date"><b>08</b><span>December</span></div><div><h5>TRENDING NEWS</h5><p>New lodges open for the spring season</p><p class="meta">Comments</p></div></div>
      <div class="news-item"><div class="date"><b>08</b><span>December</span></div><div><h5>TRENDING NEWS</h5><p>New lodges open for the spring season</p><p class="meta">Comments</p></div></div>
    </div>
  </aside>

  <footer class="footer">
    <div class="f-col">
      <h4>CONTACT INFO</h4>
      <p>Address : Pinebrook Stays Ltd<br>12 Fernhill Lane, P1<br>Phone : 01632 960 418<br>E-mail : hello@pinebrookstays.com</p>
    </div>
    <div class="f-col">
      <h4>LOCATION</h4>
      <div class="map" role="img" aria-label="Map of the holiday park location"></div>
    </div>
    <div class="f-col" style="width:135px">
      <h4>NEWSLETTER SIGN UP</h4>
      <p style="line-height:1.5">Sign up for our latest offers and holiday news.</p>
      <div class="news-input">Email address</div>
      <div class="news-btn">Subscribe</div>
    </div>
    <div class="f-col">
      <h4>SOCIAL FEED</h4>
      <div class="feed-item"><div class="feed-avatar"></div><p>Tom Ardley · Pinebrook Stays<br>New lodge photos are online<br>www.pinebrookstays.com</p></div>
      <div class="feed-item"><div class="feed-avatar"></div><p>Tom Ardley · Pinebrook Stays<br>Late deals added this week<br>www.pinebrookstays.com</p></div>
    </div>
  </footer>
  <div class="side-tab">Book Now</div>
  <div class="bottom-bar">Copyright © 2015 Pinebrook Stays. All rights reserved.</div>
</div>
</body>
</html>
```